Nano particle enhanced sprays for Chinese market

Our company is soon launching a range of nano particle-infused sprays for Chinese market. We have several different products, the main feature we want to emphasize is the nanotechnology inside, market the product as a high tech, future tech for everyday use. We also want to subtly include the fact that this is an European technology (our company is in China, however I as well as the technology are both from the EU).

The design should be minimalist, and have a sort of a “nanovibe” to it.

We have nine different products (see below), but it does not necessarily mean that we need nine different designs. Our idea is to have one general design, only change the product name, colors and a background/icon – you guys are the professionals, we will leave that to you.

Our spray can will have various sizes, you can use a 350ml with radius of 4.5 cm and height of 15 cm (the bottle print area is 14.13x15).

I have attached our previous attempt at designing the bottle, it can give you an idea – do not take any inspiration from it, I have attached another 8 pictures of a designs we actually like (labeled inspiration1….8.jpg)

I am not sure if it is of any relevance to you, but we already committed to produce 100.000 units. It should hit the shelves in early August.

I also noticed that there are some people that would close the listing just days before end so we decided to make this a guaranteed payment.

Good luck and may the force be with you!

Target Market(s)

Retail supermarket, gas stations, car supply shops.

Industry/Entity Type

It Company

Requirements
Must have
• On the front side, we want to have our company logo (can be small, see attached - change the colors and text position as you like), the product name (both English and Chinese) - see attached word file for list of product names and brief description.

The Chinese name is the most important, English brand should be secondary.

Back side is for the following information:

1: Product description
2. Usage instructions
3. Safety instructions
4. Contents
5. Legal info
5. Recycle icons, barcode

The information should be in Chinese and English. Text can be very small.
Nice to have
• This really depends on your professional judgement, it is not a request, only an option.

A one sentence product description in Chinese only. You can use the following text for as a sample – 欧洲纳米技术的热表面的瞬间冻结

and/or

Three or four highlights in either only Chinese or both English and Chinese. You can use the following as a sample:

1. 欧洲纳米技术/European Nanotechnology
2. 瞬间冻结/Instant Freeze
3. 环保/Environmentally Friendly

The product is (at this stage) targeted on Chinese market only. The only purpose of adding the English text is to enhance the feeling of a high quality product.

```html
<!DOCTYPE html>
<html lang="zh">
<head>
<meta charset="utf-8">
<title>NOVAREX Nano Spray Labels</title>
<link rel="stylesheet" href="https://fonts.googleapis.com/css2?family=Montserrat:wght@200;500;800&family=Noto+Sans+SC:wght@700&family=Noto+Serif+SC:wght@500&display=swap">
<style>
  :root {
    --bg: #0b0c0e;
    --label-black: #121213;
    --text-white: #ffffff;
    --text-soft: rgba(255, 255, 255, 0.85);
    --text-grey: #9a9a9a;
    --green-top: #55c4dc;
    --green-bottom: #68b22e;
    --green-accent: #9ad84a;
    --green-star: #5f8f3a;
    --violet-top: #6a16d8;
    --violet-bottom: #4b86dc;
    --violet-accent: #5e8ee6;
    --violet-star: #3f64a8;
    --coral-top: #f2641c;
    --coral-bottom: #ea1a80;
    --coral-accent: #f0309a;
    --coral-star: #c2257a;
  }
  html, body {
    margin: 0;
    width: 1200px;
    height: 900px;
    overflow: hidden;
    background: var(--bg);
  }
  .canvas {
    position: relative;
    width: 1200px;
    height: 900px;
    background: var(--bg);
  }
  .label {
    position: absolute;
    top: 263px;
    width: 140px;
    height: 382px;
  }
  .label--green { left: 245px; --accent: var(--green-accent); --star: var(--green-star); }
  .label--violet { left: 525px; --accent: var(--violet-accent); --star: var(--violet-star); }
  .label--coral { left: 785px; --accent: var(--coral-accent); --star: var(--coral-star); }
  .label__art {
    position: absolute;
    inset: 0;
    display: block;
  }
  .label__line {
    position: absolute;
    left: 0;
    width: 100%;
    margin: 0;
    text-align: center;
    line-height: 1;
    white-space: nowrap;
    color: var(--text-white);
  }
  .label__name-cn {
    top: 30px;
    font-family: "Noto Sans SC", sans-serif;
    font-weight: 700;
    font-size: 21px;
    letter-spacing: 1px;
  }
  .label__name-en {
    top: 58px;
    font-family: "Montserrat", sans-serif;
    font-weight: 500;
    font-size: 7px;
    letter-spacing: 1.5px;
    color: var(--text-soft);
  }
  .label__new {
    top: 86px;
    font-family: "Montserrat", sans-serif;
    font-weight: 200;
    font-size: 14px;
    letter-spacing: -0.3px;
  }
  .label__brand-mark {
    position: absolute;
    top: 113px;
    left: 60px;
    width: 20px;
    height: 17px;
    background: var(--text-white);
  }
  .label__brand {
    top: 142px;
    font-family: "Montserrat", sans-serif;
    font-weight: 800;
    font-size: 16px;
    letter-spacing: 0.3px;
  }
  .copy {
    position: absolute;
    margin: 0;
    line-height: 1;
    font-family: "Noto Serif SC", serif;
    font-weight: 500;
    white-space: nowrap;
  }
  .copy--headline { top: 286px; left: 43px; font-size: 9px; color: var(--text-white); letter-spacing: 1px; }
  .copy--tagline { font-size: 7px; color: var(--accent); letter-spacing: 0.3px; }
  .copy--tagline-1 { top: 314px; left: 45px; }
  .copy--tagline-2 { top: 326px; left: 42px; }
  .copy--feature { left: 46px; font-size: 9px; color: var(--text-grey); letter-spacing: 1px; }
  .copy--feature-1 { top: 338px; }
  .copy--feature-2 { top: 350px; }
  .star { fill: var(--star); }
</style>
</head>
<body>
<main class="canvas">

  <section class="label label--green">
    <svg class="label__art" viewBox="0 0 140 382" aria-hidden="true">
      <defs>
        <linearGradient id="fill-green" x1="0" y1="0" x2="0" y2="1">
          <stop offset="0" stop-color="var(--green-top)"/>
          <stop offset="1" stop-color="var(--green-bottom)"/>
        </linearGradient>
        <path id="star-shape" d="M0,-3.5 L1,-1.1 3.5,-1 1.6,0.6 2.2,3 0,1.7 -2.2,3 -1.6,0.6 -3.5,-1 -1,-1.1Z"/>
      </defs>
      <rect width="140" height="382" fill="var(--label-black)"/>
      <polygon points="0,0 140,0 140,230 100,262 0,215" fill="url(#fill-green)"/>
      <g class="star">
        <use href="#star-shape" x="21" y="293"/>
        <use href="#star-shape" x="11" y="305"/>
        <use href="#star-shape" x="8" y="321"/>
        <use href="#star-shape" x="13" y="337"/>
        <use href="#star-shape" x="21" y="347"/>
      </g>
    </svg>
    <p class="label__line label__name-cn">纳米速冻喷剂</p>
    <p class="label__line label__name-en">NANO FREEZE SPRAY</p>
    <p class="label__line label__new">New!</p>
    <div class="label__brand-mark"></div>
    <p class="label__line label__brand">NOVAREX</p>
    <p class="copy copy--headline">欧洲纳米技术</p>
    <p class="copy copy--tagline copy--tagline-1">欧洲纳米技术的热</p>
    <p class="copy copy--tagline copy--tagline-2">表面的瞬间冻结</p>
    <p class="copy copy--feature copy--feature-1">瞬间冻结</p>
    <p class="copy copy--feature copy--feature-2">环保</p>
  </section>

  <section class="label label--violet">
    <svg class="label__art" viewBox="0 0 140 382" aria-hidden="true">
      <defs>
        <linearGradient id="fill-violet" x1="0" y1="0" x2="0" y2="1">
          <stop offset="0" stop-color="var(--violet-top)"/>
          <stop offset="1" stop-color="var(--violet-bottom)"/>
        </linearGradient>
      </defs>
      <rect width="140" height="382" fill="var(--label-black)"/>
      <polygon points="0,0 140,0 140,230 100,262 0,215" fill="url(#fill-violet)"/>
      <g class="star">
        <use href="#star-shape" x="21" y="293"/>
        <use href="#star-shape" x="11" y="305"/>
        <use href="#star-shape" x="8" y="321"/>
        <use href="#star-shape" x="13" y="337"/>
        <use href="#star-shape" x="21" y="347"/>
      </g>
    </svg>
    <p class="label__line label__name-cn">纳米速冻喷剂</p>
    <p class="label__line label__name-en">NANO FREEZE SPRAY</p>
    <p class="label__line label__new">New!</p>
    <div class="label__brand-mark"></div>
    <p class="label__line label__brand">NOVAREX</p>
    <p class="copy copy--headline">欧洲纳米技术</p>
    <p class="copy copy--tagline copy--tagline-1">欧洲纳米技术的热</p>
    <p class="copy copy--tagline copy--tagline-2">表面的瞬间冻结</p>
    <p class="copy copy--feature copy--feature-1">瞬间冻结</p>
    <p class="copy copy--feature copy--feature-2">环保</p>
  </section>

  <section class="label label--coral">
    <svg class="label__art" viewBox="0 0 140 382" aria-hidden="true">
      <defs>
        <linearGradient id="fill-coral" x1="0" y1="0" x2="0" y2="1">
          <stop offset="0" stop-color="var(--coral-top)"/>
          <stop offset="1" stop-color="var(--coral-bottom)"/>
        </linearGradient>
      </defs>
      <rect width="140" height="382" fill="var(--label-black)"/>
      <polygon points="0,0 140,0 140,230 100,262 0,215" fill="url(#fill-coral)"/>
      <g class="star">
        <use href="#star-shape" x="21" y="293"/>
        <use href="#star-shape" x="11" y="305"/>
        <use href="#star-shape" x="8" y="321"/>
        <use href="#star-shape" x="13" y="337"/>
        <use href="#star-shape" x="21" y="347"/>
      </g>
    </svg>
    <p class="label__line label__name-cn">纳米速冻喷剂</p>
    <p class="label__line label__name-en">NANO FREEZE SPRAY</p>
    <p class="label__line label__new">New!</p>
    <div class="label__brand-mark"></div>
    <p class="label__line label__brand">NOVAREX</p>
    <p class="copy copy--headline">欧洲纳米技术</p>
    <p class="copy copy--tagline copy--tagline-1">欧洲纳米技术的热</p>
    <p class="copy copy--tagline copy--tagline-2">表面的瞬间冻结</p>
    <p class="copy copy--feature copy--feature-1">瞬间冻结</p>
    <p class="copy copy--feature copy--feature-2">环保</p>
  </section>

</main>
</body>
</html>
```